Walk Beside The River

Business Card design

Target Market(s)

People who require support in the commnity

Industry/Entity Type

Mental Health Support

Contact Information for Business Card

Mental Health Support Rosalind Tavener walkbesidetheriver@mailcove.com.au 0481 637 092 PO Box 926 Kestrel Bay QLD 4590

Colors
6B429C
8869AF
B7A5CE
E3DAEB
F3F0F8

Requirements
Must have
• Logo & details listed above
Should not have
• No red or orange

```html
<!DOCTYPE html>
<html lang="en">
<head>
<meta charset="utf-8">
<title>Walk Beside The River – Business Card</title>
<link rel="stylesheet" href="https://fonts.googleapis.com/css2?family=Open+Sans:wght@400;600;700&display=swap">
<style>
  :root {
    --stage: #2b2b2f;
    --card: #1f1e23;
    --yellow: #f1e52a;
    --purple: #6b429c;
    --purple-soft: #8869af;
    --olive: #46432f;
    --white: #f3f0f8;
  }
  * { box-sizing: border-box; margin: 0; padding: 0; }
  html, body {
    width: 1200px; height: 780px; overflow: hidden;
    background: var(--stage);
    font-family: "Open Sans", Arial, sans-serif;
  }
  .stage {
    width: 1200px; height: 780px;
    display: flex; align-items: center; justify-content: center; gap: 40px;
  }
  .card {
    position: relative;
    width: 540px; height: 330px;
    background: var(--card);
    border-radius: 24px;
    border: 3px solid var(--yellow);
    overflow: hidden;
    box-shadow: 0 18px 40px rgba(0,0,0,.45);
  }

  /* Front */
  .card-front__pattern {
    position: absolute; inset: 0;
    background: linear-gradient(160deg, #3a393f 0%, #26252a 35%, #1f1e23 60%, #1b1a1f 100%);
  }
  .card-front__brand {
    position: absolute; inset: 0;
    display: flex; align-items: center; justify-content: center; gap: 14px;
  }
  .brand-dot {
    width: 34px; height: 34px; border-radius: 50%;
    background: var(--yellow);
  }
  .card-front__name {
    color: var(--yellow); font-weight: 700; font-size: 26px; letter-spacing: .5px;
  }

  /* Back */
  .card-back__motif {
    position: absolute; right: -40px; top: -60px;
    width: 360px; height: 300px;
    background: radial-gradient(ellipse at 60% 45%, var(--olive) 0%, rgba(70,67,47,.55) 45%, rgba(31,30,35,0) 72%);
  }
  .card-back__title {
    position: absolute; right: 26px; top: 96px;
    text-align: right;
  }
  .title-row { display: flex; align-items: center; justify-content: flex-end; gap: 10px; }
  .person-name { color: var(--yellow); font-weight: 700; font-size: 26px; line-height: 1.2; }
  .title-bar { width: 14px; height: 34px; background: var(--purple); }
  .person-role { color: var(--white); font-size: 13px; margin-right: 24px; margin-top: 2px; }

  .card-back__logo {
    position: absolute; left: 30px; top: 34px;
    display: flex; align-items: center; gap: 12px;
  }
  .logo-circle { width: 62px; height: 62px; border-radius: 50%; background: var(--purple); flex: none; }
  .logo-name { color: var(--white); font-weight: 600; font-size: 14px; max-width: 110px; line-height: 1.3; }

  .card-back__service {
    position: absolute; left: 30px; top: 132px;
    color: var(--white); font-size: 15px; line-height: 1.35;
  }
  .card-back__contacts {
    position: absolute; left: 30px; bottom: 30px;
    list-style: none; color: var(--white); font-size: 14px;
  }
  .contact { display: flex; align-items: center; gap: 10px; margin-top: 6px; }
  .contact svg { width: 16px; height: 16px; flex: none; }
</style>
</head>
<body>
<main class="stage">

  <section class="card card-front" aria-label="Card front">
    <div class="card-front__pattern" role="img" aria-label="Repeating star pattern with silver highlights"></div>
    <div class="card-front__brand">
      <span class="brand-dot"></span>
      <span class="card-front__name">Walk Beside The River</span>
    </div>
  </section>

  <section class="card card-back" aria-label="Card back">
    <div class="card-back__motif" role="img" aria-label="Large faint star motif"></div>

    <div class="card-back__logo">
      <span class="logo-circle"></span>
      <span class="logo-name">Walk Beside The River</span>
    </div>

    <div class="card-back__title">
      <div class="title-row">
        <span class="person-name">Helena Marwick</span>
        <span class="title-bar"></span>
      </div>
      <p class="person-role">CEO/Director</p>
    </div>

    <p class="card-back__service">Mental Health Support<br>Rosalind Tavener</p>

    <ul class="card-back__contacts">
      <li class="contact">
        <svg viewBox="0 0 24 24" fill="none" stroke="#f1e52a" stroke-width="2.2" stroke-linecap="round" stroke-linejoin="round"><path d="M5 3h4l2 5-3 2a11 11 0 0 0 6 6l2-3 5 2v4a2 2 0 0 1-2 2A17 17 0 0 1 3 5a2 2 0 0 1 2-2z"/></svg>
        <span>0481 637 092</span>
      </li>
      <li class="contact">
        <svg viewBox="0 0 24 24" fill="none" stroke="#f1e52a" stroke-width="2.2" stroke-linejoin="round"><rect x="3" y="5" width="18" height="14" rx="2"/><path d="M3 7l9 6 9-6"/></svg>
        <span>walkbesidetheriver@mailcove.com.au</span>
      </li>
      <li class="contact">
        <svg viewBox="0 0 24 24" fill="none" stroke="#f1e52a" stroke-width="2.2" stroke-linejoin="round"><path d="M12 22s7-7 7-12a7 7 0 0 0-14 0c0 5 7 12 7 12z"/><circle cx="12" cy="10" r="2.5"/></svg>
        <span>PO Box 926 Kestrel Bay QLD 4590</span>
      </li>
    </ul>
  </section>

</main>
</body>
</html>
```